Oil and Gas Exploration and Production company needs a business card design

We need a business card design using our logo and colors in the logo. We want a mainstream design.

```html
<!DOCTYPE html>
<html lang="en">
<head>
<meta charset="utf-8">
<title>Veyra Oil &amp; Gas — Business Card</title>
<link href="https://fonts.googleapis.com/css2?family=Work+Sans:wght@400;500;700&display=swap" rel="stylesheet">
<style>
  :root {
    --backdrop: #2a2a2a;
    --card-black: #111111;
    --card-white: #ffffff;
    --gold: #c9952b;
    --text-light: #f2f2f2;
    --text-dark: #111111;
  }
  html, body {
    margin: 0;
    padding: 0;
    width: 1200px;
    height: 930px;
    overflow: hidden;
    background: var(--backdrop);
    font-family: "Work Sans", Arial, sans-serif;
  }
  .canvas {
    position: relative;
    width: 1200px;
    height: 930px;
  }
  .card {
    position: absolute;
    width: 560px;
    height: 320px;
    border-radius: 16px;
    overflow: hidden;
    background: var(--card-black);
  }
  .card--back { left: 70px; top: 100px; }
  .card--front { left: 570px; top: 510px; }

  .brand {
    display: flex;
    align-items: center;
    gap: 12px;
    font-weight: 700;
    white-space: nowrap;
  }
  .brand__dot {
    border-radius: 50%;
    background: var(--gold);
    flex: none;
  }
  .card--back .brand {
    position: absolute;
    left: 0; right: 0; top: 0; bottom: 0;
    justify-content: center;
    color: var(--card-white);
    font-size: 44px;
    letter-spacing: -0.5px;
  }
  .card--back .brand__dot { width: 34px; height: 34px; }

  .front-art {
    position: absolute;
    inset: 0;
  }
  .card--front .brand {
    position: absolute;
    right: 34px;
    top: 40px;
    color: var(--text-dark);
    font-size: 32px;
    letter-spacing: -0.3px;
  }
  .card--front .brand__dot { width: 26px; height: 26px; }

  .contact {
    position: absolute;
    left: 34px;
    bottom: 24px;
    color: var(--text-light);
  }
  .contact__name {
    margin: 0;
    color: var(--gold);
    font-size: 24px;
    font-weight: 500;
    white-space: nowrap;
  }
  .contact__title {
    margin: 2px 0 12px;
    font-size: 13px;
    letter-spacing: 0.5px;
  }
  .contact__address {
    margin: 0 0 12px;
    font-size: 14px;
    line-height: 1.35;
    font-style: normal;
  }
  .contact__list {
    list-style: none;
    margin: 0;
    padding: 0;
    font-size: 14px;
    line-height: 1.55;
  }
  .contact__list li {
    display: flex;
    align-items: center;
    gap: 8px;
  }
  .contact__icon { width: 12px; height: 12px; flex: none; }
  .contact__highlight { color: var(--gold); }
</style>
</head>
<body>
<div class="canvas">

  <section class="card card--back" aria-label="Card back">
    <div class="brand">
      <span class="brand__dot"></span>
      <span class="brand__name">Veyra Oil &amp; Gas</span>
    </div>
  </section>

  <section class="card card--front" aria-label="Card front">
    <svg class="front-art" width="560" height="320" viewBox="0 0 560 320" aria-hidden="true">
      <path d="M150,0 C175,165 340,240 560,222 L560,0 Z" fill="var(--card-white)"/>
      <path d="M142,0 C167,171 338,248 560,230" fill="none" stroke="var(--gold)" stroke-width="5"/>
    </svg>

    <div class="brand">
      <span class="brand__dot"></span>
      <span class="brand__name">Veyra Oil &amp; Gas</span>
    </div>

    <div class="contact">
      <h1 class="contact__name">Dale Harmon</h1>
      <p class="contact__title">CFO</p>
      <address class="contact__address">2150 W Ridgeline Ave,<br>Fort Worth, Texas US</address>
      <ul class="contact__list">
        <li>
          <svg class="contact__icon" viewBox="0 0 12 12" aria-hidden="true"><path d="M2.5 1 L4.5 1 L5.3 3.5 L4 4.5 C4.6 6 6 7.4 7.5 8 L8.5 6.7 L11 7.5 L11 9.5 C11 10.3 10.3 11 9.5 11 C5 11 1 7 1 2.5 C1 1.7 1.7 1 2.5 1 Z" fill="var(--gold)"/></svg>
          <span>(555) 014-2290</span>
        </li>
        <li>
          <svg class="contact__icon" viewBox="0 0 12 12" aria-hidden="true"><rect x="1" y="2.5" width="10" height="7" fill="none" stroke="var(--gold)" stroke-width="1.2"/><path d="M1 2.5 L6 6.5 L11 2.5" fill="none" stroke="var(--gold)" stroke-width="1.2"/></svg>
          <span>info@veyraoilgas.com</span>
        </li>
        <li>
          <svg class="contact__icon" viewBox="0 0 12 12" aria-hidden="true"><circle cx="6" cy="6" r="5" fill="none" stroke="var(--gold)" stroke-width="1.2"/><path d="M1 6 H11 M6 1 C3.5 3.5 3.5 8.5 6 11 M6 1 C8.5 3.5 8.5 8.5 6 11" fill="none" stroke="var(--gold)" stroke-width="1"/></svg>
          <span>www.<span class="contact__highlight">veyraoilgas</span>.com</span>
        </li>
      </ul>
    </div>
  </section>

</div>
</body>
</html>
```